Business card design for my company.
I would like the card's background colour to be black. You can also see our web site to get an idea of our brand. https://www.tmwhomecrafting.com.au/
- Name
- Email

```html
<!DOCTYPE html>
<html lang="en">
<head>
<meta charset="utf-8">
<title>TMW Home Crafting – Business Card</title>
<link rel="stylesheet" href="https://fonts.googleapis.com/css2?family=Poppins:wght@400;500;600;700&display=swap">
<style>
  :root {
    --stage: #2b2b2b;
    --card: #161616;
    --green: #0f9548;
    --white: #f2f2f2;
    --muted: #e6e6e6;
  }
  * { margin: 0; padding: 0; box-sizing: border-box; }
  html, body { width: 1200px; height: 875px; overflow: hidden; }
  body {
    background: var(--stage);
    font-family: "Poppins", sans-serif;
    display: flex;
    flex-direction: column;
    align-items: center;
    justify-content: center;
    gap: 55px;
  }
  .card {
    position: relative;
    width: 560px;
    height: 320px;
    background: var(--card);
    border-radius: 16px;
    overflow: hidden;
  }
  .brand {
    display: flex;
    align-items: center;
    gap: 12px;
    color: var(--white);
    font-weight: 700;
    letter-spacing: 0.04em;
    text-transform: uppercase;
  }
  .brand-mark { width: 16px; height: 16px; background: var(--green); }

  /* Front */
  .card-front .brand {
    position: absolute; inset: 0; justify-content: center;
    font-size: 34px;
  }
  .card-front .edge-band {
    position: absolute; left: 0; right: 0; bottom: 0; height: 7px;
    background: var(--green);
  }

  /* Back */
  .card-back .brand {
    position: absolute; top: 70px; left: 0; right: 0; justify-content: center;
    font-size: 26px;
  }
  .details {
    position: absolute; top: 150px; left: 0; right: 0;
    display: flex; justify-content: center; align-items: center; gap: 22px;
  }
  .person { text-align: right; }
  .person-name { color: var(--green); font-weight: 600; font-size: 21px; line-height: 1.1; }
  .person-title { color: var(--muted); font-size: 12px; }
  .divider { width: 1.5px; height: 52px; background: var(--green); }
  .contacts { list-style: none; color: var(--muted); font-size: 11.5px; line-height: 1.6; }
  .contacts li { display: flex; align-items: center; gap: 8px; }
  .contacts svg { width: 11px; height: 11px; fill: var(--green); flex: none; }
  .address-band {
    position: absolute; left: 0; right: 0; bottom: 0; height: 48px;
    background: var(--green); color: var(--white);
    display: flex; align-items: center; justify-content: center;
    font-size: 13px; font-weight: 500;
  }
</style>
</head>
<body>
  <section class="card card-front">
    <div class="brand"><span class="brand-mark"></span>TMW Home Crafting</div>
    <div class="edge-band"></div>
  </section>

  <section class="card card-back">
    <div class="brand"><span class="brand-mark"></span>TMW Home Crafting</div>
    <div class="details">
      <div class="person">
        <p class="person-name">Daniel Harper</p>
        <p class="person-title">CEO &amp; Founder</p>
      </div>
      <div class="divider"></div>
      <ul class="contacts">
        <li><svg viewBox="0 0 24 24"><path d="M6.6 10.8a15.1 15.1 0 0 0 6.6 6.6l2.2-2.2a1 1 0 0 1 1-.25 11.4 11.4 0 0 0 3.6.57 1 1 0 0 1 1 1V20a1 1 0 0 1-1 1A17 17 0 0 1 3 4a1 1 0 0 1 1-1h3.5a1 1 0 0 1 1 1c0 1.25.2 2.45.57 3.6a1 1 0 0 1-.25 1z"/></svg>0400 123 456</li>
        <li><svg viewBox="0 0 24 24"><path d="M2 5h20v14H2zm2 2v.5l8 5 8-5V7l-8 5z"/></svg>info@tmwhomecrafting.com.au</li>
        <li><svg viewBox="0 0 24 24"><circle cx="12" cy="12" r="10"/></svg>www.tmwhomecrafting.com.au</li>
      </ul>
    </div>
    <div class="address-band">Kingston, Hobart, TAS, Australia, Tasmania</div>
  </section>
</body>
</html>
```